Upstart Retirement Planning Firm needs help with business card design

Harborview Nest Advisors, LLC is looking for help with business card design. We give advice on investments, insurance, and other financial matters related to retirement. There are some required disclosures that we will provide but mostly we are looking for a professional, classy business card that reflects the theme we have chosen. We have a logo that is attached but we would like to add a phrase; "Turning Your Earned Income Into Retirement Income"

Doubled sided only so that we can add the required disclosures (needed for our industry) on the back of the card. We will provide the exact words for this in 1-2 days.

Target Market(s)

Retirees and Pre-retirees. Professionals 50+ years old

Industry/Entity Type

Financial Planning

Contact Information for Business Card

We currently have two people who will need separate cards so we'd like to have a template so that we can add names for new cards in the future.

For the first run, please show the following information.

Gregor Pelham, MBA, ChFC®, CLU®
Financial Advisor, Registered Representative
gpelham@harborviewnest.example
Phone: (555) 318-2946
Toll Free Fax: (800) 555-0193

Address is
2187 Meadowlark Ridge Rd.
Suite K418
Marlow Point, ME 23999

Colors
3277b5

Requirements
Must have
• Logo, contact info, small phase to describe business (in description), required legal disclosures on back of the card as follows (in small font)
• Gregor Pelham is a registered representative of and offers securities through Brightmoor Capital Brokerage Corporation, Member FNQX. Brightmoor Capital Brokerage Corporation is a member of the Brightmoor Capital Alliance which is the marketing name for Brightmoor Holding Corporation and its affiliates.
Nice to have
• Rounded edges, raised letters
Should not have
• any colors that aren't in the logo (other than black for font)

```html
<!DOCTYPE html>
<html lang="en">
<head>
<meta charset="utf-8">
<title>Harborview Nest Advisors – Business Card</title>
<link rel="stylesheet" href="https://fonts.googleapis.com/css2?family=Source+Sans+3:wght@400;600;700&display=swap">
<style>
  :root {
    --brand-blue: #3277b5;
    --silver: #b9bcc0;
    --silver-light: #dfe1e3;
    --ink: #2b2b2b;
    --ink-soft: #55585c;
    --paper: #ffffff;
    --backdrop: #ecebe8;
  }
  * { box-sizing: border-box; margin: 0; padding: 0; }
  html, body {
    width: 1200px; height: 843px; overflow: hidden;
    background: var(--backdrop);
    font-family: "Source Sans 3", "Helvetica Neue", Arial, sans-serif;
  }
  .stage {
    position: relative; width: 1200px; height: 843px;
    display: flex; align-items: center; justify-content: center; gap: 40px;
  }
  .card {
    position: relative; width: 540px; height: 309px;
    background: var(--paper); border-radius: 16px; overflow: hidden;
    box-shadow: 0 2px 8px rgba(0,0,0,0.12);
  }
  .brand-name {
    color: var(--brand-blue); font-weight: 700; text-align: center;
    letter-spacing: 0.5px;
  }

  /* back */
  .card-back .brand-name { position: absolute; top: 62px; left: 0; right: 0; font-size: 34px; }
  .card-back .tagline {
    position: absolute; top: 150px; left: 0; right: 0; text-align: center;
    color: var(--brand-blue); font-size: 18px; font-weight: 600;
  }
  .card-back .disclosure {
    position: absolute; top: 190px; left: 50px; right: 50px; text-align: center;
    color: var(--ink-soft); font-size: 12px; line-height: 1.4;
  }

  /* front */
  .card-front .band { position: absolute; inset: 0; }
  .card-front .brand-name { position: absolute; top: 30px; left: 0; right: 0; font-size: 30px; }
  .identity { position: absolute; top: 86px; left: 0; right: 0; text-align: center; }
  .identity .person { color: var(--brand-blue); font-size: 22px; font-weight: 700; }
  .identity .credentials { font-size: 15px; font-weight: 600; }
  .identity .role { color: var(--ink); font-size: 15px; margin-top: 2px; }
  .contact {
    position: absolute; left: 26px; top: 188px; list-style: none;
    color: var(--paper); font-size: 15px; line-height: 1.45;
  }
  .contact li { display: flex; align-items: center; gap: 8px; }
  .contact svg { width: 13px; height: 13px; flex: none; }
  .address {
    position: absolute; right: 26px; top: 238px; text-align: right;
    color: var(--paper); font-size: 14px; line-height: 1.35; font-style: normal;
  }
</style>
</head>
<body>
<main class="stage">

  <section class="card card-back" aria-label="Card back">
    <div class="brand-name">Harborview Nest Advisors</div>
    <p class="tagline">Turning Your Earned Income Into Retirement Income</p>
    <p class="disclosure">Gregor Pelham offers securities through Brightmoor Capital Brokerage Corporation, Member FNQX. Advice on investments, insurance and retirement income for retirees and pre-retirees. Call today to plan your next chapter with care.</p>
  </section>

  <section class="card card-front" aria-label="Card front">
    <svg class="band" viewBox="0 0 540 309" preserveAspectRatio="none" aria-hidden="true">
      <path d="M0,148 C180,158 380,185 540,205 L540,309 L0,309 Z" fill="var(--silver)"/>
      <path d="M0,154 C180,164 380,191 540,211 L540,309 L0,309 Z" fill="var(--silver-light)"/>
      <path d="M0,164 C180,174 380,201 540,221 L540,309 L0,309 Z" fill="var(--brand-blue)"/>
    </svg>
    <div class="brand-name">Harborview Nest Advisors, LLC</div>
    <div class="identity">
      <div class="person">Gregor Pelham, <span class="credentials">MBA, ChFC®, CLU®</span></div>
      <div class="role">Financial Advisor, Registered Representative</div>
    </div>
    <ul class="contact">
      <li><svg viewBox="0 0 24 24"><path fill="currentColor" d="M6.6 10.8a15 15 0 0 0 6.6 6.6l2.2-2.2c.3-.3.7-.4 1-.2 1.1.4 2.3.6 3.6.6.6 0 1 .4 1 1V20c0 .6-.4 1-1 1C10.6 21 3 13.4 3 4c0-.6.4-1 1-1h3.5c.6 0 1 .4 1 1 0 1.3.2 2.5.6 3.6.1.3 0 .7-.2 1z"/></svg>(555) 318-2946</li>
      <li><svg viewBox="0 0 24 24"><path fill="currentColor" d="M6.6 10.8a15 15 0 0 0 6.6 6.6l2.2-2.2c.3-.3.7-.4 1-.2 1.1.4 2.3.6 3.6.6.6 0 1 .4 1 1V20c0 .6-.4 1-1 1C10.6 21 3 13.4 3 4c0-.6.4-1 1-1h3.5c.6 0 1 .4 1 1 0 1.3.2 2.5.6 3.6.1.3 0 .7-.2 1z"/></svg>(800) 555-0193(Toll Free)</li>
      <li><svg viewBox="0 0 24 24"><path fill="currentColor" d="M2 5h20v14H2z"/><path fill="none" stroke="var(--brand-blue)" stroke-width="2" d="M2 5l10 8 10-8"/></svg>gpelham@harborviewnest.example</li>
    </ul>
    <address class="address">
      2187 Meadowlark Ridge Rd.<br>
      Suite K418<br>
      Marlow Point, ME 23999
    </address>
  </section>

</main>
</body>
</html>
```